Four in One (Flexible infographic for Content Management Industry)

See attachment.
A graphic depicting 4 products, where each can stand on its own and each can be combined with others, but where, if all are taken together, the best result is achieved (the "super product").
Intended use is web. See attached file as an example.
The most basic idea is as the attached diagram shows, where 4 rectangles are arranged in a quadrangle, with a middle rectangle in the center representing the combined 4 products. This concept is fine except it is a bit too obvious as it stands. We are looking for either a variation of this or another concept.
The audience is technical + professional + enterprise - NOT consumers. Hence the design should be conservative in nature.
We are aware of tools like as Canva or Pictogram where such graphics are available, but we are looking for something with a bit more imagination and flexibility.
This graphic should be targeted to web sites and be delivered with vector-based (SVG) graphics.

```html
<!DOCTYPE html>
<html lang="en">
<head>
<meta charset="utf-8">
<title>Super Product – Four in One</title>
<link rel="stylesheet" href="https://fonts.googleapis.com/css2?family=Montserrat:wght@400;500;700;800&display=swap">
<style>
  :root {
    --bg: #f6f6f6;
    --ink: #2e3340;
    --body: #2b2b2b;
    --white: #ffffff;
    --green: #8cbf43;
    --green-text: #9dc45c;
    --teal: #4cba93;
    --teal-text: #55b99a;
    --cyan: #3fc0d2;
    --cyan-text: #5cc2cd;
    --blue: #3d8fc2;
    --blue-text: #4b8fb4;
    --navy: #3a6fb5;
    --dot: #2b3045;
  }
  * { box-sizing: border-box; margin: 0; padding: 0; }
  html, body { width: 1200px; height: 626px; overflow: hidden; background: var(--bg); }
  .canvas {
    position: relative; width: 1200px; height: 626px;
    background: var(--bg);
    font-family: "Montserrat", Arial, sans-serif;
  }
  .diagram { position: absolute; left: 0; top: 0; }
  .hub-title {
    position: absolute; left: 467px; width: 254px; top: 268px;
    text-align: center; color: var(--ink); line-height: 1;
  }
  .hub-title .super { font-size: 48px; font-weight: 400; letter-spacing: 1px; display: block; }
  .hub-title .product { font-size: 25px; font-weight: 500; letter-spacing: 1px; display: block; margin-top: 4px; }

  .feature { position: absolute; width: 270px; }
  .feature--left { text-align: right; }
  .feature--right { text-align: left; }
  .feature--doc { left: 72px; top: 68px; }
  .feature--sec { left: 858px; top: 68px; }
  .feature--erp { left: 72px; top: 372px; }
  .feature--dig { left: 858px; top: 378px; }

  .feature-title { font-size: 26px; font-weight: 800; color: var(--ink); line-height: 1; letter-spacing: 0.3px; }
  .feature-sub { font-size: 14px; font-weight: 700; letter-spacing: 1px; line-height: 1; margin-top: 4px; }
  .feature--doc .feature-sub { color: var(--green-text); }
  .feature--sec .feature-sub { color: var(--teal-text); }
  .feature--erp .feature-sub { color: var(--blue-text); }
  .feature--dig .feature-sub { color: var(--cyan-text); }

  .feature-text { font-size: 12.4px; line-height: 16px; color: var(--body); margin-top: 6px; }
  .feature-list { list-style: none; margin-top: 8px; font-size: 12.4px; color: var(--body); }
  .feature-list li { height: 19px; line-height: 19px; display: flex; align-items: center; gap: 4px; }
  .feature--left .feature-list li { justify-content: flex-end; }
  .tick { width: 12px; height: 12px; flex: none; }
  .feature--left .tick { order: 2; }
</style>
</head>
<body>
<main class="canvas">
  <svg class="diagram" width="1200" height="626" viewBox="0 0 1200 626" aria-hidden="false">
    <defs>
      <filter id="soft-shadow" x="-30%" y="-30%" width="160%" height="160%">
        <feDropShadow dx="0" dy="3" stdDeviation="6" flood-color="#000" flood-opacity="0.12"/>
      </filter>
    </defs>

    <!-- outer ring segments -->
    <g class="ring" fill="none" stroke-width="2.5">
      <path d="M486.5 126.8 A215 215 0 0 1 681.5 116.6" stroke="var(--green)" opacity="0.7"/>
      <path d="M780.2 205.5 A215 215 0 0 1 790.4 400.5" stroke="var(--teal)"/>
      <path d="M701.5 499.2 A215 215 0 0 1 506.5 509.4" stroke="var(--cyan)" opacity="0.8"/>
      <path d="M407.8 420.5 A215 215 0 0 1 397.6 225.5" stroke="var(--blue)"/>
    </g>
    <g class="ring-dots" fill="var(--dot)">
      <circle cx="681.5" cy="116.6" r="5"/>
      <circle cx="790.4" cy="400.5" r="5"/>
      <circle cx="506.5" cy="509.4" r="5"/>
      <circle cx="397.6" cy="225.5" r="5"/>
    </g>

    <!-- connectors -->
    <g class="connectors" stroke-width="82" stroke-linecap="butt">
      <line x1="442" y1="161" x2="594" y2="313" stroke="var(--green)"/>
      <line x1="746" y1="161" x2="594" y2="313" stroke="var(--teal)"/>
      <line x1="442" y1="465" x2="594" y2="313" stroke="var(--blue)"/>
      <line x1="746" y1="465" x2="594" y2="313" stroke="var(--cyan)"/>
    </g>

    <!-- hub -->
    <circle class="hub" cx="594" cy="313" r="127" fill="var(--white)" filter="url(#soft-shadow)"/>
    <g class="hub-dashes">
      <rect x="545" y="347" width="11" height="5" fill="var(--green)"/>
      <rect x="563" y="347" width="13" height="5" fill="var(--teal)"/>
      <rect x="584" y="346" width="18" height="7" fill="var(--cyan)"/>
      <rect x="610" y="347" width="13" height="5" fill="var(--blue)"/>
      <rect x="631" y="347" width="11" height="5" fill="var(--navy)"/>
    </g>

    <!-- product nodes -->
    <g class="nodes" fill="var(--white)" filter="url(#soft-shadow)">
      <circle cx="438" cy="160" r="54"/>
      <circle cx="748" cy="160" r="54"/>
      <circle cx="438" cy="466" r="54"/>
      <circle cx="748" cy="466" r="54"/>
    </g>
    <g class="node-icons">
      <circle role="img" aria-label="Icon: browser window with folders and a gear" cx="438" cy="160" r="28" fill="var(--green)" opacity="0.22"/>
      <circle role="img" aria-label="Icon: documents with a shield and padlock" cx="748" cy="160" r="28" fill="var(--teal)" opacity="0.22"/>
      <circle role="img" aria-label="Icon: office building with finance and people symbols" cx="438" cy="466" r="28" fill="var(--blue)" opacity="0.22"/>
      <circle role="img" aria-label="Icon: monitor showing a chart with circuit lines" cx="748" cy="466" r="28" fill="var(--cyan)" opacity="0.22"/>
    </g>
  </svg>

  <div class="hub-title">
    <span class="super">SUPER</span>
    <span class="product">PRODUCT</span>
  </div>

  <section class="feature feature--left feature--doc">
    <h2 class="feature-title">DOCUMENT</h2>
    <p class="feature-sub">MANAGEMENT</p>
    <p class="feature-text">Streamline document organization, access, and collaboration with easier file storage and sharing, leading to more efficient workflows.</p>
    <ul class="feature-list">
      <li>Centralized Document Control <svg class="tick" viewBox="0 0 12 12"><circle cx="6" cy="6" r="5" fill="none" stroke="var(--green)" stroke-width="1.4"/><path d="M3.2 6.2 5.2 8.2 10.5 2.5" fill="none" stroke="var(--green)" stroke-width="1.8"/></svg></li>
      <li>Collaborative Workspace Integration <svg class="tick" viewBox="0 0 12 12"><circle cx="6" cy="6" r="5" fill="none" stroke="var(--green)" stroke-width="1.4"/><path d="M3.2 6.2 5.2 8.2 10.5 2.5" fill="none" stroke="var(--green)" stroke-width="1.8"/></svg></li>
      <li>Automated Compliance Tracking <svg class="tick" viewBox="0 0 12 12"><circle cx="6" cy="6" r="5" fill="none" stroke="var(--green)" stroke-width="1.4"/><path d="M3.2 6.2 5.2 8.2 10.5 2.5" fill="none" stroke="var(--green)" stroke-width="1.8"/></svg></li>
      <li>Check 4 <svg class="tick" viewBox="0 0 12 12"><circle cx="6" cy="6" r="5" fill="none" stroke="var(--green)" stroke-width="1.4"/><path d="M3.2 6.2 5.2 8.2 10.5 2.5" fill="none" stroke="var(--green)" stroke-width="1.8"/></svg></li>
    </ul>
  </section>

  <section class="feature feature--right feature--sec">
    <h2 class="feature-title">SECURITY</h2>
    <p class="feature-sub">COMPLIANCE</p>
    <p class="feature-text">Benefit from tailored cloud solutions, secure data storage, and expert disaster recovery planning for reliable and scalable IT operations.</p>
    <ul class="feature-list">
      <li><svg class="tick" viewBox="0 0 12 12"><circle cx="6" cy="6" r="5" fill="none" stroke="var(--teal)" stroke-width="1.4"/><path d="M3.2 6.2 5.2 8.2 10.5 2.5" fill="none" stroke="var(--teal)" stroke-width="1.8"/></svg> Custom Cloud Solutions</li>
      <li><svg class="tick" viewBox="0 0 12 12"><circle cx="6" cy="6" r="5" fill="none" stroke="var(--teal)" stroke-width="1.4"/><path d="M3.2 6.2 5.2 8.2 10.5 2.5" fill="none" stroke="var(--teal)" stroke-width="1.8"/></svg> Secure Data Storage</li>
      <li><svg class="tick" viewBox="0 0 12 12"><circle cx="6" cy="6" r="5" fill="none" stroke="var(--teal)" stroke-width="1.4"/><path d="M3.2 6.2 5.2 8.2 10.5 2.5" fill="none" stroke="var(--teal)" stroke-width="1.8"/></svg> Expert Disaster Recovery</li>
      <li><svg class="tick" viewBox="0 0 12 12"><circle cx="6" cy="6" r="5" fill="none" stroke="var(--teal)" stroke-width="1.4"/><path d="M3.2 6.2 5.2 8.2 10.5 2.5" fill="none" stroke="var(--teal)" stroke-width="1.8"/></svg> Check 4</li>
    </ul>
  </section>

  <section class="feature feature--left feature--erp">
    <h2 class="feature-title">ENTERPRISE</h2>
    <p class="feature-sub">RESOURCE PLANNING</p>
    <p class="feature-text">Simplify management across finance, sales, and operations, enabling better decision-making and improved productivity.</p>
    <ul class="feature-list">
      <li>Integrated Business Processes <svg class="tick" viewBox="0 0 12 12"><circle cx="6" cy="6" r="5" fill="none" stroke="var(--blue)" stroke-width="1.4"/><path d="M3.2 6.2 5.2 8.2 10.5 2.5" fill="none" stroke="var(--blue)" stroke-width="1.8"/></svg></li>
      <li>Enhanced Decision-Making <svg class="tick" viewBox="0 0 12 12"><circle cx="6" cy="6" r="5" fill="none" stroke="var(--blue)" stroke-width="1.4"/><path d="M3.2 6.2 5.2 8.2 10.5 2.5" fill="none" stroke="var(--blue)" stroke-width="1.8"/></svg></li>
      <li>Productivity Improvement <svg class="tick" viewBox="0 0 12 12"><circle cx="6" cy="6" r="5" fill="none" stroke="var(--blue)" stroke-width="1.4"/><path d="M3.2 6.2 5.2 8.2 10.5 2.5" fill="none" stroke="var(--blue)" stroke-width="1.8"/></svg></li>
      <li>Check 4 <svg class="tick" viewBox="0 0 12 12"><circle cx="6" cy="6" r="5" fill="none" stroke="var(--blue)" stroke-width="1.4"/><path d="M3.2 6.2 5.2 8.2 10.5 2.5" fill="none" stroke="var(--blue)" stroke-width="1.8"/></svg></li>
    </ul>
  </section>

  <section class="feature feature--right feature--dig">
    <h2 class="feature-title">DIGITITAL</h2>
    <p class="feature-sub">TRANSFORMATION</p>
    <p class="feature-text">Turn scanned documents into easily searchable digital archives, boosting efficiency and accessibility.</p>
    <ul class="feature-list">
      <li><svg class="tick" viewBox="0 0 12 12"><circle cx="6" cy="6" r="5" fill="none" stroke="var(--cyan)" stroke-width="1.4"/><path d="M3.2 6.2 5.2 8.2 10.5 2.5" fill="none" stroke="var(--cyan)" stroke-width="1.8"/></svg> Instant searchable Archives with OCR</li>
      <li><svg class="tick" viewBox="0 0 12 12"><circle cx="6" cy="6" r="5" fill="none" stroke="var(--cyan)" stroke-width="1.4"/><path d="M3.2 6.2 5.2 8.2 10.5 2.5" fill="none" stroke="var(--cyan)" stroke-width="1.8"/></svg> Automated Document Classification</li>
      <li><svg class="tick" viewBox="0 0 12 12"><circle cx="6" cy="6" r="5" fill="none" stroke="var(--cyan)" stroke-width="1.4"/><path d="M3.2 6.2 5.2 8.2 10.5 2.5" fill="none" stroke="var(--cyan)" stroke-width="1.8"/></svg> TeamVault and Cloud Bloh Readv</li>
      <li><svg class="tick" viewBox="0 0 12 12"><circle cx="6" cy="6" r="5" fill="none" stroke="var(--cyan)" stroke-width="1.4"/><path d="M3.2 6.2 5.2 8.2 10.5 2.5" fill="none" stroke="var(--cyan)" stroke-width="1.8"/></svg> Check 4</li>
    </ul>
  </section>
</main>
</body>
</html>
```